Business card for marketing analytics company

Need a business card for new company. I have a logo already that I want to be built into the card and should use those colours

Company is called steered by tallies
Design must bring steered by tallies to life not be a card that could be for anyone with a logo put on it.

Like the front to be fairly clean and uncluttered bringing the logo out with a suitable design on the back of the card.

The logo represents a compass and business growth so those themes along with numbers, analytics , data are appropriate.
I'm often working with creative industries so also needs to reflect the creative side of analytics rather than be very corporate looking.

Target Market(s)

Ad agency, media agency, consumer goods clients

Industry/Entity Type

Market Research

Contact Information for Business Card

Needs to include name, title, email and phone number

Colors
f78f20
f68d4d
ec1f27

Requirements
Must have
• Must bring steered by tallies to life not be a card that could be for anyone with a logo put on it.
• Logo, Correct colours
• Like a design on the back that relates to company name
• Designs for both sides
Should not have
• Please do not just submit logo and a coloured card.
• It needs to have a design element to it
• No black background
• No clear cards - needs front & back

```html
<!DOCTYPE html>
<html lang="en">
<head>
<meta charset="utf-8">
<title>Steered by Tallies — Business Card</title>
<link rel="stylesheet" href="https://fonts.googleapis.com/css2?family=Work+Sans:wght@400;500;600;700&display=swap">
<style>
  :root {
    --page-bg: #e4e4e6;
    --card-grey: #6a6a6a;
    --card-grey-mark: #747474;
    --card-white: #ffffff;
    --brand-orange: #f37424;
    --brand-orange-light: #f78f20;
    --brand-red: #ec1f27;
    --brand-deep-red: #c42a2a;
    --text-dark: #4a4f55;
    --text-muted: #5a5a5a;
    --white: #ffffff;
  }
  * { box-sizing: border-box; margin: 0; padding: 0; }
  html, body {
    width: 1200px; height: 1000px; overflow: hidden;
    background: var(--page-bg);
    font-family: "Work Sans", Arial, sans-serif;
  }
  .canvas { position: relative; width: 1200px; height: 1000px; }

  .card { position: absolute; overflow: hidden; box-shadow: 0 6px 18px rgba(0,0,0,0.18); }

  /* Back side */
  .card-back {
    left: 300px; top: 40px; width: 620px; height: 354px;
    background: var(--card-grey);
  }
  .card-back .watermark-ring {
    position: absolute; left: 250px; top: 30px;
    width: 300px; height: 300px; border-radius: 50%;
    border: 10px solid var(--card-grey-mark);
  }
  .card-back .brand {
    position: absolute; left: 110px; top: 118px;
    display: flex; align-items: center; gap: 30px;
  }
  .card-back .brand-dot {
    width: 110px; height: 110px; border-radius: 50%;
    border: 4px solid var(--white);
  }
  .card-back .brand-name {
    color: var(--white); font-weight: 500; font-size: 38px; line-height: 1.05;
    letter-spacing: 1px;
  }

  /* Front side */
  .card-front {
    left: 160px; top: 432px; width: 880px; height: 503px;
    background: var(--card-white);
  }
  .name-block { position: absolute; left: 52px; top: 62px; display: flex; gap: 14px; }
  .name-marker { width: 8px; display: flex; flex-direction: column; }
  .name-marker span:first-child { height: 22px; background: var(--brand-red); }
  .name-marker span:last-child { height: 14px; background: var(--brand-orange-light); }
  .person-name { color: var(--brand-red); font-weight: 700; font-size: 27px; line-height: 1; letter-spacing: 0.5px; }
  .person-title { color: var(--brand-orange); font-weight: 600; font-size: 16px; margin-top: 6px; letter-spacing: 0.5px; }

  .card-front .brand {
    position: absolute; left: 560px; top: 118px;
    display: flex; align-items: center; gap: 22px;
  }
  .card-front .brand-dot {
    width: 82px; height: 82px; border-radius: 50%;
    border: 4px solid var(--brand-orange);
  }
  .card-front .brand-name {
    color: var(--text-dark); font-weight: 500; font-size: 29px; line-height: 1.05;
    letter-spacing: 0.5px;
  }

  .address {
    position: absolute; left: 92px; top: 190px;
    color: var(--text-muted); font-size: 19px; line-height: 1.3; letter-spacing: 0.5px;
  }

  .contact-band {
    position: absolute; left: 0; top: 262px; width: 720px; height: 168px;
    background: var(--brand-orange);
    clip-path: polygon(0 0, 100% 0, 92% 100%, 0 100%);
  }
  .contact-list { list-style: none; position: absolute; left: 72px; top: 22px; }
  .contact-list li {
    display: flex; align-items: center; gap: 18px;
    color: var(--white); font-size: 19px; height: 34px; letter-spacing: 0.5px;
  }
  .contact-list svg { width: 18px; height: 18px; fill: none; stroke: var(--white); stroke-width: 2; }

  .band-end-ring {
    position: absolute; left: 632px; top: 300px;
    width: 176px; height: 176px; border-radius: 50%;
    background: var(--card-white);
    border: 8px solid var(--card-white);
    box-shadow: inset 0 0 0 6px var(--brand-deep-red);
  }
</style>
</head>
<body>
<main class="canvas">

  <section class="card card-back" aria-label="Card back">
    <div class="watermark-ring" aria-hidden="true"></div>
    <div class="brand">
      <div class="brand-dot"></div>
      <div class="brand-name">Steered by<br>&nbsp;&nbsp;&nbsp;&nbsp;Tallies</div>
    </div>
  </section>

  <section class="card card-front" aria-label="Card front">
    <div class="name-block">
      <div class="name-marker"><span></span><span></span></div>
      <div>
        <h1 class="person-name">DANIEL ROWE</h1>
        <p class="person-title">FOUNDER</p>
      </div>
    </div>

    <div class="brand">
      <div class="brand-dot"></div>
      <div class="brand-name">Steered by<br>&nbsp;&nbsp;Tallies</div>
    </div>

    <p class="address">your street address,<br>suite-123, country-1230</p>

    <div class="contact-band">
      <ul class="contact-list">
        <li>
          <svg viewBox="0 0 20 20" aria-hidden="true"><path d="M3 7c0-2 2-3 7-3s7 1 7 3v1h-4V6.5H7V8H3z"/><rect x="4" y="9" width="12" height="8" rx="1"/><circle cx="10" cy="13" r="2"/></svg>
          <span>000 000 0000</span>
        </li>
        <li>
          <svg viewBox="0 0 20 20" aria-hidden="true"><rect x="2" y="5" width="16" height="11"/><path d="M2 5l8 6 8-6"/></svg>
          <span>hello@tallymail.co</span>
        </li>
        <li>
          <svg viewBox="0 0 20 20" aria-hidden="true"><circle cx="12" cy="8" r="5"/><path d="M8.5 11.5L3 17"/></svg>
          <span>www.tallysite.co</span>
        </li>
      </ul>
    </div>

    <div class="band-end-ring" aria-hidden="true"></div>
  </section>

</main>
</body>
</html>
```